Now Leasing Banner

Looking for a banner that says the following information approx 4' x 30'

Now Leasing Maplebrook Terrace 925-318-6042

Target Market(s)

Drive by traffic

Industry/Entity Type

Residential property management

Requirements
Must have
• Clear and readable from a distance

```html
<!DOCTYPE html>
<html lang="en">
<head>
<meta charset="utf-8">
<title>Now Leasing Banner – Maplebrook Terrace</title>
<link rel="stylesheet" href="https://fonts.googleapis.com/css2?family=Jost:wght@600;700&display=swap">
<style>
  :root {
    --backdrop: #a9a6a7;
    --banner-white: #ffffff;
    --navy: #231f5e;
    --teal: #13a89b;
    --teal-outline: #1aa39a;
  }
  html, body {
    margin: 0;
    padding: 0;
    width: 1200px;
    height: 879px;
    overflow: hidden;
    background: var(--backdrop);
  }
  .canvas {
    position: relative;
    width: 1200px;
    height: 879px;
  }
  .banner {
    position: absolute;
    left: 40px;
    top: 364px;
    width: 1120px;
    height: 150px;
    filter: drop-shadow(14px 14px 10px rgba(0, 0, 0, 0.35));
  }
  .banner svg { display: block; }
  .banner-text {
    font-family: "Jost", "Futura", sans-serif;
    fill: var(--navy);
    stroke: var(--teal-outline);
    paint-order: stroke;
    filter: drop-shadow(3px 3px 2px rgba(0, 0, 0, 0.3));
  }
  .headline { font-size: 118px; font-weight: 600; stroke-width: 1.6px; }
  .property-name { font-size: 34px; font-weight: 700; stroke-width: 0.8px; }
  .phone { font-size: 44px; font-weight: 700; stroke-width: 0.9px; }
  .band-teal { fill: var(--teal); }
  .band-navy { fill: var(--navy); stroke: var(--banner-white); stroke-width: 2px; }
  .banner-field { fill: var(--banner-white); }
</style>
</head>
<body>
<main class="canvas">
  <section class="banner" aria-label="Now Leasing banner for Maplebrook Terrace">
    <svg width="1120" height="150" viewBox="0 0 1120 150" xmlns="http://www.w3.org/2000/svg">
      <rect class="banner-field" x="0" y="0" width="1120" height="150"/>
      <path class="band-teal" d="M0,90 C150,120 320,136 570,135 C800,134 1000,104 1120,105 L1120,150 L0,150 Z"/>
      <path class="band-navy" d="M0,117 C200,140 400,146 570,143 C800,139 1000,113 1120,112 L1120,152 L0,152 Z"/>
      <text class="banner-text headline" x="30" y="106" textLength="732" lengthAdjust="spacingAndGlyphs">NOW LEASING</text>
      <text class="banner-text property-name" x="784" y="46" textLength="310" lengthAdjust="spacingAndGlyphs">Maplebrook Terrace</text>
      <text class="banner-text phone" x="780" y="99" textLength="318" lengthAdjust="spacingAndGlyphs">925-318-6042</text>
    </svg>
  </section>
</main>
</body>
</html>
```